Business Card Design

I need business cards designed for a new company i have started that makes cakes, particularly themed kids cakes with a really modern design and I would like to have my business cards reflect this. I have attached some photos of cakes I have made and would like some to be used.

Industry/Entity Type

Business

Contact Information for Business Card

Business Name: Tarts and Treats by Maren
Mobile: 0492 815 063
email: maren@tartsandtreatsbymaren.example.au
Instagram: instagram.com/tartsandtreatsbymaren/
Facebook: fb.me/tartsandtreatsbymaren

Colors
e667a6
b768aa
3276b5

Requirements
Must have
• Business Name: Tarts and Treats by Maren
• Mobile: 0492 815 063
• email: maren@tartsandtreatsbymaren.example.au
• Instagram: instagram.com/tartsandtreatsbymaren/
• Facebook: fb.me/tartsandtreatsbymaren
Nice to have
• 2 to 3 pictures of my cakes

```html
<!DOCTYPE html>
<html lang="en">
<head>
<meta charset="utf-8">
<title>Tarts and Treats by Maren – Business Cards</title>
<link rel="stylesheet" href="https://fonts.googleapis.com/css2?family=Open+Sans:wght@400;600;700&display=swap">
<style>
  :root {
    --backdrop: #ece8e4;
    --pink: #e667a6;
    --pink-deep: #d9589a;
    --pink-light: #ef8cbf;
    --purple: #b768aa;
    --purple-light: #c88bc0;
    --white: #ffffff;
    --ink: #6a6a6a;
    --shadow: rgba(60, 40, 50, 0.18);
  }
  html, body {
    margin: 0;
    padding: 0;
    width: 1200px;
    height: 843px;
    overflow: hidden;
    background: var(--backdrop);
    font-family: "Open Sans", sans-serif;
  }
  .canvas {
    position: relative;
    width: 1200px;
    height: 843px;
  }
  .card {
    position: absolute;
    top: 266px;
    width: 540px;
    height: 310px;
    border-radius: 4px;
    overflow: hidden;
    box-shadow: 0 10px 28px var(--shadow);
  }
  /* Back of card */
  .card-back {
    left: 40px;
    background: linear-gradient(120deg, var(--pink-deep) 0%, var(--pink) 45%, var(--pink-light) 60%, var(--pink-deep) 100%);
    display: flex;
    align-items: center;
    justify-content: center;
  }
  .wordmark {
    display: flex;
    align-items: center;
    gap: 10px;
    font-weight: 600;
    line-height: 1.1;
  }
  .wordmark-dot {
    width: 14px;
    height: 14px;
    border-radius: 50%;
    flex: none;
  }
  .card-back .wordmark { color: var(--white); font-size: 34px; }
  .card-back .wordmark-dot { background: var(--white); }

  /* Front of card */
  .card-front {
    left: 620px;
    background: var(--white);
  }
  .card-front .wave {
    position: absolute;
    left: 0;
    top: 0;
    width: 540px;
    height: 310px;
  }
  .person {
    position: absolute;
    left: 38px;
    top: 26px;
    color: var(--white);
  }
  .person-name {
    margin: 0;
    font-size: 17px;
    font-weight: 700;
    letter-spacing: 0.5px;
  }
  .person-role {
    margin: 2px 0 0;
    font-size: 12px;
  }
  .contact {
    position: absolute;
    left: 30px;
    bottom: 52px;
    margin: 0;
    padding: 0;
    list-style: none;
    font-size: 11.5px;
    color: var(--ink);
  }
  .contact li {
    display: flex;
    align-items: center;
    gap: 8px;
    margin-top: 6px;
  }
  .contact svg { width: 13px; height: 13px; flex: none; }
  .card-front .wordmark {
    position: absolute;
    right: 34px;
    top: 160px;
    color: var(--purple);
    font-size: 22px;
    text-align: right;
    max-width: 230px;
  }
  .card-front .wordmark-dot { background: var(--pink); }
  .social {
    position: absolute;
    right: 24px;
    bottom: 30px;
    margin: 0;
    padding: 0;
    list-style: none;
    font-size: 12px;
    color: var(--ink);
  }
  .social li {
    display: flex;
    align-items: center;
    justify-content: flex-end;
    gap: 8px;
    margin-top: 5px;
  }
  .social-mark {
    width: 12px;
    height: 12px;
    background: var(--pink);
    border-radius: 2px;
  }
</style>
</head>
<body>
<main class="canvas">

  <section class="card card-back" aria-label="Business card back">
    <div class="wordmark">
      <span class="wordmark-dot"></span>
      <span>Tarts and Treats by Maren</span>
    </div>
  </section>

  <section class="card card-front" aria-label="Business card front">
    <svg class="wave" viewBox="0 0 540 310" aria-hidden="true">
      <defs>
        <linearGradient id="band" x1="0" y1="0" x2="1" y2="0">
          <stop offset="0" stop-color="#c98fc2"/>
          <stop offset="0.5" stop-color="#b768aa"/>
          <stop offset="1" stop-color="#a85a9c"/>
        </linearGradient>
      </defs>
      <path d="M0,0 H540 V170 C450,158 380,120 280,122 C180,124 100,96 0,78 Z" fill="#e667a6"/>
      <path d="M0,0 H540 V160 C450,148 380,110 280,112 C180,114 100,86 0,68 Z" fill="#ffffff"/>
      <path d="M0,0 H540 V156 C450,144 380,106 280,108 C180,110 100,82 0,64 Z" fill="url(#band)"/>
    </svg>

    <div class="person">
      <p class="person-name">JONAS REED</p>
      <p class="person-role">CEO/Founder</p>
    </div>

    <ul class="contact">
      <li>
        <svg viewBox="0 0 14 14" aria-hidden="true"><rect x="3" y="0.5" width="8" height="13" rx="1.5" fill="none" stroke="#e667a6" stroke-width="1.4"/><circle cx="7" cy="11" r="0.9" fill="#e667a6"/></svg>
        <span>0492 815 063</span>
      </li>
      <li>
        <svg viewBox="0 0 14 14" aria-hidden="true"><rect x="0.5" y="2.5" width="13" height="9" rx="1" fill="#e667a6"/><path d="M1,3 L7,8 L13,3" fill="none" stroke="#ffffff" stroke-width="1.2"/></svg>
        <span>maren@tartsandtreatsbymaren.example.au</span>
      </li>
    </ul>

    <div class="wordmark">
      <span class="wordmark-dot"></span>
      <span>Tarts and Treats by Maren</span>
    </div>

    <ul class="social">
      <li><span>tartsandtreatsbymaren</span><span class="social-mark"></span></li>
      <li><span>tartsandtreatsbymaren</span><span class="social-mark"></span></li>
    </ul>
  </section>

</main>
</body>
</html>
```